Package Design - Disposable Face Towel

Hi,

We are needing assistance with graphic design on our box/carton/package.

The attached image that is white is our biggest competitor.

Our brand is "VELMORA BATH CO." Please see the logo we uploaded.

Oder we have in mind for front of box:

Logo
LARGE TOWELS
50 Count
Ultra Soft| 100% USDA Bio-Based|100% Eucalyptus Viscose | Vegan
VELMORABATHCO.COM

We like medium to dark blue on most of the box, with white and minimal hot pink or salmon. Something that is sharp, modern, and stands out from our competitors.

Box dimensions are: 6.25 x 5.25 x 4.75 inches

This will be 1 of many design projects.

Target Market(s)

Female Beauty Products

Font styles to use
Serif
Sans Serif

Colors
0054AA
0677BA
7BADD7
CADEEF
E8F1F8
EB3D1F
EC4F4E
F09395
F8D3D4
FCEDEE

Requirements
Must have
• Needs to look sharp and modern

```html
<!DOCTYPE html>
<html lang="en">
<head>
<meta charset="utf-8">
<title>Velmora Bath Co. – Large Towels XL Carton Dieline</title>
<link rel="stylesheet" href="https://fonts.googleapis.com/css2?family=Marcellus&family=Montserrat:wght@300;400;700&display=swap">
<style>
  :root {
    --carton-blue: #0096db;
    --fold-line: #8fb4d0;
    --towel-white: #f1f2f4;
    --cut-line: #b9c3cc;
    --ink-white: #ffffff;
    --brand-blue: #08a6e6;
    --page: #ffffff;
  }
  html, body {
    margin: 0;
    padding: 0;
    width: 982px;
    height: 1200px;
    overflow: hidden;
    background: var(--page);
  }
  .dieline { display: block; width: 982px; height: 1200px; }
  .panel { fill: var(--carton-blue); }
  .fold { fill: none; stroke: var(--fold-line); stroke-width: 0.7; }
  .window-guide { fill: none; stroke: #d7e6f2; stroke-width: 0.7; stroke-dasharray: 3 2; }
  .towel-peek { fill: var(--towel-white); }
  .dispenser-cut { fill: none; stroke: var(--cut-line); stroke-width: 0.8; }
  .brand-name {
    font-family: "Marcellus", serif;
    letter-spacing: 1px;
    text-anchor: middle;
  }
  .brand-name--lid { fill: var(--ink-white); font-size: 25px; }
  .brand-name--towel { fill: var(--brand-blue); font-size: 17px; }
  .front-copy { font-family: "Montserrat", sans-serif; fill: var(--ink-white); }
  .product-title { font-weight: 700; font-size: 11.5px; text-anchor: middle; }
  .tagline { font-weight: 400; font-size: 7.4px; text-anchor: middle; letter-spacing: 0.3px; }
  .spec { font-weight: 400; font-size: 7.2px; letter-spacing: 0.2px; }
  .count { font-weight: 700; font-size: 8.6px; letter-spacing: 0.3px; }
  .size { font-weight: 300; font-size: 6px; }
  .web { font-weight: 300; font-size: 7.6px; text-anchor: middle; letter-spacing: 0.4px; }
  .rule { stroke: var(--ink-white); stroke-width: 0.6; }
  .rule--bold { stroke-width: 1.4; }
</style>
</head>
<body>
<svg class="dieline" viewBox="0 0 982 1200" xmlns="http://www.w3.org/2000/svg">
  <!-- back wall (top) -->
  <rect class="panel" x="313" y="0" width="356" height="300"/>

  <!-- side walls with glue tabs -->
  <path class="panel" d="M42 302 H22 A21 21 0 0 0 1 323 V580 A21 21 0 0 0 22 601 H42 Z"/>
  <rect class="panel" x="42" y="300" width="271" height="300"/>
  <rect class="panel" x="669" y="300" width="271" height="300"/>
  <path class="panel" d="M940 302 H960 A21 21 0 0 1 981 323 V580 A21 21 0 0 1 960 601 H940 Z"/>

  <!-- top lid -->
  <rect class="panel" x="313" y="300" width="356" height="300"/>

  <!-- front face with dust flaps -->
  <path class="panel" d="M313 600 H298 A26 26 0 0 0 272 626 V874 A26 26 0 0 0 298 900 H313 Z"/>
  <rect class="panel" x="313" y="600" width="356" height="300"/>
  <path class="panel" d="M669 600 H684 A26 26 0 0 1 710 626 V874 A26 26 0 0 1 684 900 H669 Z"/>

  <!-- bottom -->
  <rect class="panel" x="313" y="900" width="356" height="300"/>

  <!-- fold lines -->
  <path class="fold" d="M313 300 H669 M42 300 H940 M42 600 H940 M313 900 H669 M42 300 V600 M940 300 V600 M313 300 V900 M669 300 V900"/>

  <!-- lid branding -->
  <text class="brand-name brand-name--lid" x="491" y="393">VELMORA BATH CO.</text>

  <!-- dispenser window guide -->
  <rect class="window-guide" x="367" y="450" width="248" height="281"/>

  <!-- towel showing through -->
  <polygon class="towel-peek" points="313,600 669,600 491,778" role="img" aria-label="Textured white towel folded into a point, visible through the carton front"/>
  <text class="brand-name brand-name--towel" x="491" y="677">VELMORA BATH CO.</text>

  <!-- perforated dispenser opening -->
  <path class="dispenser-cut" d="M367 731 L357 723 Q341 731 341 749 Q341 768 357 775 L367 767 L372 772 L390 772 L395 769 L398 771 L412 771 L417 768 L420 770 L434 770 L439 767 L442 769 L456 769 L461 766 L464 768 L477 768 L483 770 L491 778 L499 770 L505 768 L518 768 L521 766 L526 769 L540 769 L543 767 L548 770 L562 770 L565 768 L570 771 L584 771 L587 769 L592 772 L610 772 L615 767 L625 775 Q640 768 640 749 Q640 731 625 723 L615 731 L610 726 L598 726 L593 728 L588 726 L577 726 L572 728 L556 728 L551 726 L540 726 L535 728 L520 728 L515 726 L500 726 L495 728 L487 728 L482 726 L467 726 L462 728 L446 728 L441 726 L430 726 L425 728 L409 728 L404 726 L393 726 L388 728 L372 728 Z"/>

  <!-- front copy -->
  <g class="front-copy">
    <text class="product-title" x="491" y="815">LARGE TOWELS XL</text>
    <text class="tagline" x="491" y="827">Nature’s best gift to your skin</text>
    <text class="tagline" x="491" y="836.5">wrapped in a soft, absorbent towel</text>
    <line class="rule" x1="379" y1="845" x2="602" y2="845"/>
    <text class="spec" x="378.5" y="856">Ultra Soft | 100% USDA  Bio-based</text>
    <text class="spec" x="378.5" y="865">100%  Eucalyptus  Viscose  |  Vegan</text>
    <line class="rule rule--bold" x1="521" y1="849" x2="521" y2="867"/>
    <text class="count" x="537.5" y="856">50 COUNT</text>
    <text class="size" x="537.5" y="864.5">Size: 10inch x 12inch</text>
    <line class="rule" x1="379" y1="871" x2="602" y2="871"/>
    <text class="web" x="491" y="884">VELMORABATHCO.COM</text>
  </g>
</svg>
</body>
</html>
```